Business Card Design

I already have a company logo for my company. I have a logo for the manufacturer we represent. I want a professional business card design.

```html
<!DOCTYPE html>
<html lang="en">
<head>
<meta charset="utf-8">
<title>Beacon Alert Group – Business Card</title>
<link href="https://fonts.googleapis.com/css2?family=Montserrat:wght@400;500;700;800&display=swap" rel="stylesheet">
<style>
  :root{
    --backdrop:#2b2b2d;
    --card-dark:#141414;
    --card-light:#ffffff;
    --brand-red:#e3262b;
    --ink:#2a2a2a;
    --silver:#cfcfcf;
    --gold:#c9a227;
  }
  *{margin:0;padding:0;box-sizing:border-box}
  html,body{width:1200px;height:688px;overflow:hidden}
  body{
    background:var(--backdrop);
    font-family:"Montserrat",sans-serif;
    position:relative;
  }
  .card{
    position:absolute;
    top:196px;
    width:520px;height:297px;
    border-radius:4px;
    box-shadow:0 18px 40px rgba(0,0,0,.45);
    overflow:hidden;
  }
  .card--front{left:50px;background:var(--card-dark)}
  .card--back{left:630px;background:var(--card-light)}

  .brand{
    display:flex;align-items:center;gap:10px;
    font-weight:800;letter-spacing:.5px;text-transform:uppercase;
  }
  .brand__mark{width:18px;height:18px;background:var(--brand-red)}
  .card--front .brand{
    position:absolute;left:50%;top:50%;transform:translate(-50%,-50%);
    color:var(--silver);font-size:26px;
  }

  .card--back .brand{
    position:absolute;left:34px;top:70px;
    color:var(--brand-red);font-size:22px;
  }
  .brand-rule{
    position:absolute;left:34px;top:106px;width:232px;height:3px;background:var(--gold);
  }

  .person{position:absolute;left:34px;top:136px}
  .person__name{color:var(--brand-red);font-weight:700;font-size:20px}
  .person__role{color:var(--ink);font-size:11px;margin-top:2px}

  .address{position:absolute;left:34px;top:190px;color:var(--ink);font-size:11px;line-height:15px}

  .contacts{position:absolute;left:34px;top:234px;list-style:none;color:var(--ink);font-size:11px;line-height:16px}
  .contacts li{display:flex;align-items:center;gap:8px}
  .contacts svg{width:9px;height:9px;fill:var(--brand-red)}
</style>
</head>
<body>
  <section class="card card--front" aria-label="Card front">
    <div class="brand"><span class="brand__mark"></span>Beacon Alert Group</div>
  </section>

  <section class="card card--back" aria-label="Card back">
    <div class="brand">Beacon Alert Group</div>
    <div class="brand-rule"></div>

    <div class="person">
      <p class="person__name">Daniel Reyes</p>
      <p class="person__role">Managing Director</p>
    </div>

    <address class="address" style="font-style:normal">
      2840 Larkspur Ave<br>Denver, CO 80219
    </address>

    <ul class="contacts">
      <li>
        <svg viewBox="0 0 10 10"><path d="M2 0h2l1 2.5-1.3 1a6 6 0 0 0 2.8 2.8l1-1.3L10 6v2a2 2 0 0 1-2 2A8 8 0 0 1 0 2a2 2 0 0 1 2-2z"/></svg>
        555.301.7748
      </li>
      <li>
        <svg viewBox="0 0 10 10"><path d="M0 2h10v6H0z M0 2l5 3.5L10 2" stroke="#fff" stroke-width=".8"/></svg>
        info@beaconalertgroup.com
      </li>
      <li>
        <svg viewBox="0 0 10 10"><circle cx="5" cy="5" r="5"/><path d="M0 5h10M5 0c-2.5 3-2.5 7 0 10M5 0c2.5 3 2.5 7 0 10" stroke="#fff" stroke-width=".7" fill="none"/></svg>
        www.beaconalertgroup.com
      </li>
    </ul>
  </section>
</body>
</html>
```